Kettleby Twins Playing Cards

We are wanting a cool design for a playing card that includes our logo(s). I will attach our two logos, we are open to using either one of them or another version of them. I will also attach some pictures of card decks to use for inspiration. These are just decks that we have seen from other artists that we liked. We are located in West Texas so although not necessary, a Sotol or Agave or cactus or quail (bird) or some sort of sunset would pay homage to our surroundings. I realize the examples are all very different, but those are just some decks that we like! Thank you!

```html
<!DOCTYPE html>
<html lang="en">
<head>
<meta charset="utf-8">
<title>Kettleby Twins Playing Cards</title>
<link rel="stylesheet" href="https://fonts.googleapis.com/css2?family=Oswald:wght@600&display=swap">
<style>
  :root {
    --bg: #222222;
    --card-black: #050607;
    --gold-light: #fbe3a6;
    --gold: #e6bd5f;
    --gold-deep: #a67a2c;
    --gold-dark: #5c3f12;
  }
  * { margin: 0; padding: 0; box-sizing: border-box; }
  html, body { width: 1200px; height: 900px; overflow: hidden; background: var(--bg); }
  .canvas {
    position: relative;
    width: 1200px; height: 900px;
    display: flex; align-items: center; justify-content: center; gap: 110px;
  }
  .card {
    position: relative;
    width: 380px; height: 532px;
    background: var(--card-black);
    border-radius: 24px;
  }
  .card__frame {
    position: absolute; inset: 10px;
    border: 3px solid var(--gold);
    border-radius: 16px;
  }
  .card__frame--inner { inset: 24px; border-width: 2px; border-radius: 10px; }

  /* Card back */
  .back__pattern {
    position: absolute; inset: 22px;
    border-radius: 12px;
    background:
      radial-gradient(circle at 50% 45%, var(--gold-light) 0%, var(--gold) 30%, var(--gold-deep) 65%, var(--gold-dark) 100%);
  }
  .back__emblem {
    position: absolute; left: 50%; top: 50%;
    transform: translate(-50%, -50%);
    display: flex; align-items: center; gap: 12px;
    padding: 14px 22px;
    background: var(--card-black);
    border-radius: 10px;
  }
  .back__emblem-dot {
    width: 18px; height: 18px; border-radius: 50%;
    background: var(--gold);
  }
  .back__name {
    font-family: "Oswald", sans-serif;
    font-weight: 600;
    font-size: 30px;
    letter-spacing: 1px;
    text-transform: uppercase;
    color: var(--gold);
    white-space: nowrap;
  }

  /* Card face */
  .face__index {
    position: absolute;
    display: flex; flex-direction: column; align-items: center;
    font-family: "Oswald", sans-serif;
    font-weight: 600; font-size: 40px; line-height: 1;
    color: var(--gold);
  }
  .face__index svg { width: 24px; height: 24px; margin-top: 6px; }
  .face__index--top { left: 40px; top: 38px; }
  .face__index--bottom { right: 40px; bottom: 38px; transform: rotate(180deg); }
  .face__pip {
    position: absolute;
    width: 66px; height: 66px;
    transform: translate(-50%, -50%);
  }
  .face__pip--down { transform: translate(-50%, -50%) rotate(180deg); }
</style>
</head>
<body>
<svg width="0" height="0" style="position:absolute">
  <defs>
    <linearGradient id="gold-fill" x1="0" y1="1" x2="1" y2="0">
      <stop offset="0" stop-color="#a67a2c"/>
      <stop offset="0.5" stop-color="#e6bd5f"/>
      <stop offset="1" stop-color="#fbe3a6"/>
    </linearGradient>
    <symbol id="spade" viewBox="0 0 100 100">
      <path fill="url(#gold-fill)" d="M50 4 C30 30 5 44 5 64 C5 82 23 92 39 85 C43 83 45 80 47 77 C46 87 40 95 31 100 L69 100 C60 95 54 87 53 77 C55 80 57 83 61 85 C77 92 95 82 95 64 C95 44 70 30 50 4 Z"/>
    </symbol>
  </defs>
</svg>

<main class="canvas">
  <section class="card card--back">
    <div class="card__frame"></div>
    <div class="back__pattern" role="img" aria-label="Ornate gold and black paisley and floral lace pattern"></div>
    <div class="back__emblem">
      <span class="back__emblem-dot"></span>
      <span class="back__name">Kettleby Twins</span>
    </div>
  </section>

  <section class="card card--face" aria-label="Nine of spades">
    <div class="card__frame"></div>
    <div class="card__frame card__frame--inner"></div>

    <div class="face__index face__index--top">9<svg><use href="#spade"/></svg></div>
    <div class="face__index face__index--bottom">9<svg><use href="#spade"/></svg></div>

    <svg class="face__pip" style="left:31%;top:20%"><use href="#spade"/></svg>
    <svg class="face__pip" style="left:31%;top:40%"><use href="#spade"/></svg>
    <svg class="face__pip face__pip--down" style="left:31%;top:60%"><use href="#spade"/></svg>
    <svg class="face__pip face__pip--down" style="left:31%;top:80%"><use href="#spade"/></svg>
    <svg class="face__pip" style="left:50%;top:50%"><use href="#spade"/></svg>
    <svg class="face__pip" style="left:69%;top:20%"><use href="#spade"/></svg>
    <svg class="face__pip" style="left:69%;top:40%"><use href="#spade"/></svg>
    <svg class="face__pip face__pip--down" style="left:69%;top:60%"><use href="#spade"/></svg>
    <svg class="face__pip face__pip--down" style="left:69%;top:80%"><use href="#spade"/></svg>
  </section>
</main>
</body>
</html>
```